Flyer for handout on the street to attract people

Create two different leaflets for handing out to recruit volunteers to participate in a program of biological specimen donation. The leaflet should be catchy, have some graphics, and have enough info that people will want to sign up by going to the website for more information.

Leave room on each leaflet for some English and Chinese. The example of Leaflet #1 will need approximately the same space in order to have the Chinese translation.

The example of Leaflet #2 already has a Chinese translation which can be incorporated.

The size should be half of A4 page. If it is a whole A4 page it may also be considered.

Leaflet #1 Text:

RECRUITING HEALTHY VOLUNTEERS (and get PAID)!

The Orient Floracell Reserve is recruiting healthy individuals in Hong Kong to participate in a scientific research project to study bacteria in healthy guts. They will pay you $200 HKD per day to participate in the study. If you qualify, you can earn up to $4800 a month!

Incidences of digestive and colon diseases are increasing rapidly in Hong Kong, and part of the key to solving this problem is understanding gut bacteria. There are up to 100 trillion bacteria and microbes in every human gut, including yours. Scientists have recently uncovered that these bacteria are key human digestion and immune systems. However, when your gut bacteria are imbalanced, it can cause all kinds of problems such as indigestion, IBS, ulcerative colitis, or clostridium difficile infection.

Every year, more than 500,000 people are infected by a toxic bacteria called clostridium difficile, which causes severe stomach pain, and sometimes even death. YOUR GUT BACTERIA COULD BE KEY TO HELPING THESE SICK PATIENTS.

CRITERIA FOR PARTICIPATING: If you are a healthy adult between 18-50 years old; no digestive problems and no recent medications, then the Orient VitaVault needs your participation! They will pay you $200 HKD per day to participate in the study. If you qualify, you can earn up to $4800 a month! To learn more information, go to http://www.orientvitavault.example or send a whatsapp to 7342 9086

Leaflet #2 Text:

Get paid to give your poopoo!

Literally.

Asia’s first commercial stool bank is recruiting donors. Get paid up to $4,800 HKD per month for your poop donations at our convenient Central Hong Kong lab.

Answer the questionnaire to see if you qualify at www.orientvitavault.example or call 7342 9086 for more information.

你好屎!

我地就係想要你D好屎。

全亞洲第一間商業糞便銀行正招募捐贈者。請即前往我們位於中環的糞便銀行成為捐贈者,每月最多可賺取6,000港元的酬勞。

想知道自己是否適合捐贈?馬上點擊 www.orientvitavault.example/donate 回答問題或撥打0000-0000查詢詳情。

Target Market(s)

Young professionals, middle-class

Industry/Entity Type

Medical

Font styles to use
Serif
Sans Serif
Decorative

Requirements
Must have
• The text. Two leaflet examples. Some graphics.
Nice to have
• Catchy design. Something people will see while walking past and go ahead and take it from someone handing out flyers.
Should not have
• Only text. Should be colorful and have graphics. (Can download or shutterstock photos.)

```html
<!DOCTYPE html>
<html lang="en">
<head>
<meta charset="utf-8">
<title>Volunteer Recruitment Leaflets</title>
<link href="https://fonts.googleapis.com/css2?family=Oswald:wght@500;700&family=Open+Sans:wght@400;600;700&family=Alfa+Slab+One&family=Noto+Sans+TC:wght@400;700&display=swap" rel="stylesheet">
<style>
:root{
  --blue:#1f3fd8;
  --blue-deep:#1530a8;
  --blue-soft:#6f86f0;
  --ink:#2b2b3a;
  --grey-text:#4a4a55;
  --paper:#ffffff;
  --paper-shade:#eef0f4;
  --photo-light:#dfe6ee;
  --photo-mid:#b9c7d6;
  --stage:#e4e5e8;
}
*{box-sizing:border-box;margin:0;padding:0}
html,body{width:1200px;height:1200px;overflow:hidden}
body{background:linear-gradient(180deg,#f1f1f3,var(--stage));font-family:"Open Sans",sans-serif;color:var(--ink);position:relative}
.leaflet{position:absolute;left:50px;width:1100px;height:540px;background:var(--paper);box-shadow:0 12px 30px rgba(0,0,0,.18);overflow:hidden}
.leaflet--recruit{top:40px}
.leaflet--donate{top:620px}
.deco{position:absolute;left:0;top:0;width:550px;height:540px}
.panel{position:absolute;top:0;height:100%;width:550px}
.panel--left{left:0}
.panel--right{left:550px;background:linear-gradient(180deg,#fff 0%,var(--paper-shade) 100%)}
.divider{position:absolute;left:549px;top:40px;width:3px;height:460px;background:var(--blue)}
.brand{position:absolute;display:flex;align-items:center;gap:8px;font-weight:600;font-size:15px;color:var(--blue);white-space:nowrap}
.brand::before{content:"";width:16px;height:16px;border-radius:50%;background:var(--blue)}
.photo{position:absolute;background:linear-gradient(160deg,var(--photo-light),var(--photo-mid))}
.circle{position:absolute;border-radius:50%;border:7px solid var(--blue-soft);box-shadow:0 0 0 3px #fff inset;background:radial-gradient(circle at 45% 40%,#f4f6f9,var(--photo-mid))}

/* leaflet 1 */
.recruit-title{position:absolute;left:40px;top:40px;font-family:"Oswald",sans-serif;line-height:1;color:var(--ink)}
.recruit-title span{display:block}
.recruit-title .t1,.recruit-title .t3{font-size:26px;font-weight:500}
.recruit-title .t2{font-size:42px;font-weight:700;color:var(--blue)}
.recruit-title .t4{font-size:26px;font-weight:700;color:var(--blue)}
.recruit-body{position:absolute;left:40px;top:272px;width:470px;font-size:11px;line-height:1.5;color:var(--grey-text)}
.recruit-body p{margin-bottom:7px}
.recruit-body .callout{color:var(--blue);font-weight:600;text-transform:uppercase;letter-spacing:.5px}
.criteria{position:absolute;right:24px;top:28px;width:340px;text-align:right}
.criteria h2{font-family:"Oswald",sans-serif;font-size:22px;line-height:1.05;color:var(--blue);font-weight:700;margin-bottom:8px}
.criteria ul{list-style:none;font-size:10px;line-height:1.45;color:var(--grey-text)}
.criteria li{margin-bottom:2px;white-space:nowrap}
.criteria li::after{content:"";display:inline-block;width:6px;height:6px;background:var(--blue);border-radius:50%;margin-left:6px;vertical-align:middle}
.learn{position:absolute;left:20px;top:192px;width:510px;font-size:10px;line-height:1.45;color:var(--blue);border-top:2px solid var(--blue);padding-top:6px}
.recruit-stool{position:absolute;left:20px;top:380px;width:220px;font-size:10.5px;font-weight:600;color:var(--grey-text);line-height:1.4}
.recruit-band-text{position:absolute;left:285px;top:442px;width:250px;color:#fff;font-weight:700;font-size:13px;line-height:1.4}

/* leaflet 2 */
.donate-title{position:absolute;left:36px;top:72px;font-family:"Alfa Slab One",serif;color:var(--blue-deep);line-height:1}
.donate-title span{display:block}
.donate-title .big{font-size:40px}
.donate-title .small{font-size:22px;color:var(--ink);margin-top:4px}
.donate-en{position:absolute;left:40px;top:292px;width:470px;font-size:11.5px;line-height:1.5;color:var(--grey-text)}
.donate-en p{margin-bottom:6px}
.donate-zh{position:absolute;left:40px;top:416px;width:470px;font-family:"Noto Sans TC",sans-serif;font-size:11.5px;line-height:1.55;color:var(--grey-text);border-top:2px solid var(--blue);padding-top:8px}
.zh-pill{position:absolute;left:20px;top:30px;width:510px;padding:9px 16px;border-radius:24px;background:var(--blue);color:#fff;font-family:"Noto Sans TC",sans-serif;font-size:11px;line-height:1.45}
</style>
</head>
<body>

<section class="leaflet leaflet--recruit" aria-label="Leaflet one: recruiting healthy volunteers">
  <div class="panel panel--left">
    <svg class="deco" viewBox="0 0 550 540" aria-hidden="true">
      <path d="M0 240 C240 250 390 140 430 0 L550 0 L550 0 C500 60 460 140 400 200 C330 260 180 275 0 262 Z" fill="#f3f4f7"/>
      <path d="M0 250 C250 260 400 150 440 0" fill="none" stroke="var(--blue)" stroke-width="9"/>
      <path d="M330 150 C400 110 450 60 470 0" fill="none" stroke="var(--blue)" stroke-width="4"/>
    </svg>
    <h1 class="recruit-title">
      <span class="t1">RECRUITING</span>
      <span class="t2">HEALTHY</span>
      <span class="t3">VOLUNTEERS</span>
      <span class="t4">AND GET PAID</span>
    </h1>
    <div class="brand" style="left:300px;top:222px">Orient Floracell Reserve</div>
    <div class="recruit-body">
      <p>The Orient Floracell Reserve is recruiting healthy individuals in Hong Kong to participate in a scientific research project to study bacteria in healthy guts. They will pay you $200 HKD per day to participate in the study. If you qualify, you can earn up to $4800 a month!</p>
      <p>Incidences of digestive and colon diseases are increasing rapidly in Hong Kong, and part of the key to solving this problem is understanding gut bacteria. There are up to 100 trillion bacteria and microbes in every human gut, including yours. Scientists have recently uncovered that these bacteria are key human digestion and immune systems. However, when your gut bacteria are imbalanced, it can cause all kinds of problems such as indigestion, IBS, ulcerative colitis, or clostridium difficile infection.</p>
      <p>Every year, more than 500,000 people are infected by a toxic bacteria called clostridium difficile, which causes severe stomach pain, and sometimes even death.</p>
      <p class="callout">Your gut bacteria could be key to helping these sick patients.</p>
    </div>
  </div>
  <div class="divider"></div>
  <div class="panel panel--right">
    <div class="photo" style="left:20px;top:20px;width:130px;height:110px;border-radius:0 0 60px 0" role="img" aria-label="Photo of a smiling medical team in white coats"></div>
    <div class="criteria">
      <h2>CRITERIA FOR<br>PARTICIPATING</h2>
      <ul>
        <li>If you are a healthy adult between 18-50 years old</li>
        <li>No digestive problems and no recent medications</li>
        <li>Then the Orient VitaVault needs your participation!</li>
        <li>They will pay you $200 HKD per day to participate</li>
        <li>If you qualify, you can earn up to $4800 a month!</li>
      </ul>
    </div>
    <p class="learn">To learn more information, go to http://www.orientvitavault.example or send a whatsapp to 7342 9086</p>
    <div class="circle" style="left:15px;top:235px;width:120px;height:120px" role="img" aria-label="Circular photo of a doctor with a patient"></div>
    <div class="circle" style="left:150px;top:245px;width:125px;height:125px" role="img" aria-label="Circular photo of a group of doctors"></div>
    <div class="circle" style="left:290px;top:235px;width:115px;height:115px" role="img" aria-label="Circular photo of medical staff reviewing a clipboard"></div>
    <div class="photo" style="left:425px;top:250px;width:110px;height:75px;border-radius:4px" role="img" aria-label="Photo of a laptop showing a doctor with a green medical cross"></div>
    <svg class="deco" viewBox="0 0 550 540" aria-hidden="true">
      <path d="M0 540 L0 520 C150 515 250 430 350 395 C430 365 500 355 550 350 L550 540 Z" fill="var(--blue)"/>
      <path d="M0 511 C150 506 250 421 350 386 C430 356 500 346 550 341" fill="none" stroke="#fff" stroke-width="4"/>
    </svg>
    <p class="recruit-stool">Asia’s first commercial stool bank is recruiting donors. Get paid up to $4,800 HKD per month for your poop donations at our convenient Central Hong Kong lab.</p>
    <p class="recruit-band-text">Answer the questionnaire to see if you qualify at www.orientvitavault.example or call 7342 9086 for more information.</p>
  </div>
</section>

<section class="leaflet leaflet--donate" aria-label="Leaflet two: get paid to donate">
  <div class="panel panel--left">
    <div class="photo" style="left:310px;top:0;width:240px;height:130px;background:linear-gradient(160deg,#fff,var(--photo-light))" role="img" aria-label="Photo of three smiling doctors in white coats"></div>
    <svg class="deco" viewBox="0 0 550 540" aria-hidden="true">
      <path d="M0 40 C100 30 200 20 300 0 L0 0 Z" fill="#f3f4f7"/>
      <path d="M0 250 C180 262 330 250 400 200 C460 160 520 140 550 130" fill="none" stroke="var(--blue)" stroke-width="8"/>
      <path d="M0 262 C160 272 300 268 360 240" fill="none" stroke="var(--blue)" stroke-width="3"/>
    </svg>
    <h1 class="donate-title"><span class="big">Get paid to</span><span class="small">give your poopoo!</span></h1>
    <div class="brand" style="left:70px;top:182px">Orient Floracell Reserve</div>
    <div class="donate-en">
      <p>Literally.</p>
      <p>Asia’s first commercial stool bank is recruiting donors. Get paid up to $4,800 HKD per month for your poop donations at our convenient Central Hong Kong lab.</p>
      <p>Answer the questionnaire to see if you qualify at www.orientvitavault.example or call 7342 9086 for more information.</p>
    </div>
    <div class="donate-zh" lang="zh-Hant">
      <p>你好屎！</p>
      <p>我地就係想要你D好屎。</p>
      <p>全亞洲第一間商業糞便銀行正招募捐贈者。請即前往我們位於中環的糞便銀行成為捐贈者，每月最多可賺取6,000港元的酬勞。</p>
    </div>
  </div>
  <div class="divider"></div>
  <div class="panel panel--right">
    <p class="zh-pill" lang="zh-Hant">想知道自己是否適合捐贈？馬上點擊 www.orientvitavault.example/donate 回答問題或撥打0000-0000查詢詳情。</p>
    <svg class="deco" viewBox="0 0 550 540" aria-hidden="true">
      <path d="M0 540 C150 520 280 420 330 300 C360 220 420 140 550 110 L550 540 Z" fill="var(--blue)"/>
      <path d="M0 530 C150 510 270 410 320 295 C350 215 410 130 550 100" fill="none" stroke="#fff" stroke-width="4"/>
    </svg>
    <div class="photo" style="left:400px;top:110px;width:140px;height:200px;border-radius:60px 60px 0 0" role="img" aria-label="Photo of a doctor in a white coat with stethoscope"></div>
    <div class="circle" style="left:250px;top:140px;width:145px;height:145px" role="img" aria-label="Circular photo of a smiling medical team"></div>
    <div class="circle" style="left:90px;top:270px;width:185px;height:185px" role="img" aria-label="Circular photo of a doctor and a smiling patient"></div>
  </div>
</section>

</body>
</html>
```